Media Services Start-up -- Corporate Website and Logo Design. Inspiration required!

We need a logo design and corporate website design, including coding, for our start-up business.
Vennatra’s value proposition is based on bringing together media content from a vast number of geographies globally, adding human and AI curation, translation and editing, and delivering the content using tailored customer interfaces. On the one hand, the business brings together media coverage from all over the world, and on the other it brings together content, human skills and technology to deliver a supreme customer experience.
Vennatra is a B2B media monitoring and analytics business with emphasis on global customers. Vennatra's service offering is centred around sourcing media content from different markets, processing, storing and delivering the content and insights derived from it using an online platform / mobile app.
The messaging we want to create through the logo is:
- Global scope
- Speed of delivery
- Cost-efficiency
- Multi-lingual
- Tailor-made
- Trustworthy
Target Market(s)
Business to business, PR / Communications, Media, Marketing
Logo Text
Vennatra
Coding
Coded - Design and coding required
Number of Pages Required
5+ page
Font styles to use
Other font styles liked:
- See Design Brief for details
Colors
Designer to choose colors to be used in the design.

```html
<!DOCTYPE html>
<html lang="en">
<head>
<meta charset="utf-8">
<title>Vennatra — Global Media Intelligence</title>
<link href="https://fonts.googleapis.com/css2?family=Roboto:wght@400;500;700&display=swap" rel="stylesheet">
<style>
  :root {
    --teal: #3bb39e;
    --ink: #000000;
    --white: #ffffff;
    --field-border: #555555;
    --placeholder: #5a5a5a;
    --hero-deep: #14191e;
    --hero-mid: #2b3a44;
    --hero-glow: #3e5a66;
  }
  * { box-sizing: border-box; margin: 0; padding: 0; }
  html, body { width: 1200px; height: 747px; overflow: hidden; }
  body { font-family: "Roboto", sans-serif; background: var(--white); position: relative; }

  .site-header {
    position: absolute; left: 0; top: 0; width: 1200px; height: 71px;
    background: var(--white);
  }
  .brand {
    position: absolute; left: 143px; top: 15px;
    font-size: 31px; font-weight: 700; color: var(--ink); letter-spacing: -0.3px;
  }
  .main-nav a {
    position: absolute; top: 26px; font-size: 14px; color: var(--ink);
    text-decoration: none;
  }
  .sign-in {
    position: absolute; left: 967px; top: 18px; width: 92px; height: 35px;
    background: var(--teal); color: var(--white); border-radius: 2px;
    font-size: 15px; display: flex; align-items: center; justify-content: center;
    box-shadow: 0 2px 5px rgba(0,0,0,0.2);
  }

  .hero {
    position: absolute; left: 0; top: 71px; width: 1200px; height: 632px;
  }
  .hero-backdrop {
    position: absolute; inset: 0;
    background:
      radial-gradient(ellipse 420px 260px at 600px 230px, var(--hero-glow), transparent 70%),
      radial-gradient(ellipse 700px 500px at 500px 350px, var(--hero-mid), var(--hero-deep) 85%);
  }
  .hero-copy { position: absolute; left: 140px; top: 196px; width: 520px; color: var(--white); }
  .hero-title {
    font-size: 40px; font-weight: 700; line-height: 58px; letter-spacing: 0.2px;
  }
  .hero-text {
    margin-top: 22px; width: 460px; font-size: 17px; line-height: 25.4px; font-weight: 400;
  }

  .lead-card {
    position: absolute; left: 766px; top: 155px; width: 293px; height: 322px;
    background: var(--white); border-radius: 4px; padding: 3.5px;
    box-shadow: 0 2px 8px rgba(0,0,0,0.3);
  }
  .lead-card h2 {
    height: 48px; background: var(--ink); color: var(--white);
    font-size: 17px; font-weight: 500; display: flex; align-items: center; justify-content: center;
    border-radius: 2px 2px 0 0;
  }
  .field {
    position: absolute; left: 32px; width: 228px; height: 37px;
    border: 1px solid var(--field-border); border-radius: 3px;
    font-size: 12.5px; color: var(--placeholder); padding-left: 13px;
    display: flex; align-items: center;
  }
  .cta {
    position: absolute; left: 57px; top: 255px; width: 178px; height: 36px;
    background: var(--teal); color: var(--white); font-size: 15px;
    display: flex; align-items: center; justify-content: center;
    border-radius: 2px; box-shadow: 0 1px 3px rgba(0,0,0,0.2);
  }

  .site-footer {
    position: absolute; left: 0; top: 703px; width: 1200px; height: 44px;
    background: var(--teal);
  }
  .copyright {
    position: absolute; left: 143px; top: 14px; font-size: 13px; color: var(--white);
  }
  .social { position: absolute; top: 11px; width: 23px; height: 23px; border-radius: 50%; background: var(--ink); }
</style>
</head>
<body>
  <header class="site-header">
    <div class="brand">Vennatra</div>
    <nav class="main-nav">
      <a style="left:363px">Home</a>
      <a style="left:455px">Solutions</a>
      <a style="left:568px">How We Do It</a>
      <a style="left:707px">Our People</a>
      <a style="left:829px">Our Technology</a>
    </nav>
    <div class="sign-in">SIGN IN</div>
  </header>

  <section class="hero">
    <div class="hero-backdrop" role="img" aria-label="Dark photo of a business person holding a tablet, overlaid with a globe and social network connection icons"></div>
    <div class="hero-copy">
      <h1 class="hero-title">DELIVERING GLOBAL MEDIA INTELLIGENCE</h1>
      <p class="hero-text">Vennatra is an international media intelligence service provider. We help communications teams builds and operate truly global media monitoring and measurement programmes.</p>
    </div>

    <form class="lead-card">
      <h2>Learn More About Vennatra</h2>
      <div class="field" style="top:81px">Name</div>
      <div class="field" style="top:138px">Email Address</div>
      <div class="field" style="top:194px">Phone</div>
      <div class="cta">GET STARTED</div>
    </form>
  </section>

  <footer class="site-footer">
    <div class="copyright">© 2019 Vennatra Analytics Media. All rights reserved.</div>
    <span class="social" style="left:952px" aria-label="Social link"></span>
    <span class="social" style="left:980px" aria-label="Social link"></span>
    <span class="social" style="left:1008px" aria-label="Social link"></span>
    <span class="social" style="left:1036px" aria-label="Feed link"></span>
  </footer>
</body>
</html>
```